Veldmark Supplies Business Card

Professional business card that stand out to our potential customers. Front and back with clean modern design

Industry/Entity Type

Oil and gas

Contact Information for Business Card

Name, address, website , office phone and cell number

Requirements
Must have
• Editable files for each employee

```html
<!DOCTYPE html>
<html lang="en">
<head>
<meta charset="utf-8">
<title>Veldmark Supplies Business Card</title>
<link rel="stylesheet" href="https://fonts.googleapis.com/css2?family=Montserrat:wght@400;500;700&display=swap">
<style>
  :root {
    --bg: #2b2b2d;
    --cyan: #0bb0d1;
    --cyan-deep: #0897b4;
    --band-blue: #30a9cb;
    --band-red: #ec2227;
    --white: #ffffff;
    --ink: #1d1d1f;
    --red-brand: #e52228;
  }
  * { margin: 0; padding: 0; box-sizing: border-box; }
  html, body {
    width: 1200px; height: 875px; overflow: hidden;
    background: var(--bg);
    font-family: "Montserrat", sans-serif;
  }
  .sheet {
    width: 1200px; height: 875px;
    display: flex; flex-direction: column;
    align-items: center; justify-content: center; gap: 40px;
  }
  .card {
    position: relative;
    width: 620px; height: 354px;
    border-radius: 22px;
    overflow: hidden;
    box-shadow: 0 14px 30px rgba(0,0,0,.45);
  }

  /* Back */
  .card--back { background: var(--cyan); display: flex; align-items: center; justify-content: center; }
  .back-mark { display: flex; align-items: center; gap: 14px; }
  .back-mark__square { width: 34px; height: 34px; background: var(--cyan-deep); }
  .back-mark__name {
    font-weight: 700; font-size: 30px; letter-spacing: 2px;
    text-transform: uppercase; color: var(--cyan-deep);
  }

  /* Front */
  .card--front { background: var(--white); }
  .brand {
    position: absolute; top: 54px; right: 40px;
    display: flex; align-items: center; gap: 10px;
  }
  .brand__square { width: 20px; height: 20px; background: var(--red-brand); }
  .brand__name {
    font-weight: 700; font-size: 18px; letter-spacing: 1px;
    text-transform: uppercase; color: var(--red-brand);
  }
  .band-blue {
    position: absolute; left: 282px; right: 0; top: 118px; height: 98px;
    background: var(--band-blue);
  }
  .band-red {
    position: absolute; left: 0; width: 282px; top: 166px; height: 92px;
    background: var(--band-red);
    display: flex; flex-direction: column; align-items: flex-end; justify-content: center;
    padding-right: 18px; color: var(--white);
  }
  .person__name { font-weight: 700; font-size: 23px; line-height: 1.1; }
  .person__title { font-weight: 400; font-size: 13px; margin-top: 2px; }
  .contacts {
    position: absolute; left: 300px; top: 126px;
    list-style: none; color: var(--ink);
  }
  .contacts li {
    display: flex; align-items: center; gap: 8px;
    font-size: 12.5px; line-height: 20px;
  }
  .contacts svg { width: 11px; height: 11px; flex: none; }
  .address {
    position: absolute; left: 170px; top: 278px;
    font-size: 13.5px; color: var(--ink);
  }
</style>
</head>
<body>
<main class="sheet">

  <section class="card card--back" aria-label="Card back">
    <div class="back-mark">
      <span class="back-mark__square"></span>
      <span class="back-mark__name">Veldmark Supplies</span>
    </div>
  </section>

  <section class="card card--front" aria-label="Card front">
    <div class="brand">
      <span class="brand__square"></span>
      <span class="brand__name">Veldmark Supplies</span>
    </div>

    <div class="band-blue"></div>

    <div class="band-red">
      <span class="person__name">Tarek Holloway</span>
      <span class="person__title">President</span>
    </div>

    <ul class="contacts">
      <li>
        <svg viewBox="0 0 12 12" aria-hidden="true"><rect x="1" y="4" width="10" height="7" rx="1" fill="#fff"/><path d="M1 4 Q6 0 11 4" stroke="#fff" stroke-width="1.4" fill="none"/></svg>
        +1.555.210.4400 x123
      </li>
      <li>
        <svg viewBox="0 0 12 12" aria-hidden="true"><path d="M2 1 L4.5 1 L5.5 3.5 L4 4.8 Q5 7 7.2 8 L8.5 6.5 L11 7.5 L11 10 Q6 11 2.5 7.5 Q1 5 2 1 Z" fill="#fff"/></svg>
        +1.555.019.782
      </li>
      <li>
        <svg viewBox="0 0 12 12" aria-hidden="true"><rect x="1" y="2.5" width="10" height="7" fill="#fff"/><path d="M1 2.5 L6 6.5 L11 2.5" stroke="#30a9cb" stroke-width="1" fill="none"/></svg>
        info@veldmarksupplies.com
      </li>
      <li>
        <svg viewBox="0 0 12 12" aria-hidden="true"><circle cx="6" cy="6" r="5" fill="#fff"/><path d="M1 6 H11 M6 1 Q3 6 6 11 M6 1 Q9 6 6 11" stroke="#30a9cb" stroke-width=".9" fill="none"/></svg>
        www.veldmarksupplies.com
      </li>
    </ul>

    <p class="address">42 Lantern Square Ashbury, NJ 07000 USA</p>
  </section>

</main>
</body>
</html>
```